Kestrova - presentation for a remote DBA team offering data platform management

We need a website design for wordpress site called Kestrova.cz
We deliver remote database and data platform administration and development, oversee the database administrators, consult and train the personnel responsible for the database operations. The website should include several sections, home page with graphics elements supporting the name and service - remote dba work; blog section; service introduction and description, team introduction and description, download section for documents, presentations etc.

Target Market(s)

small and medium business companies requiring remote DBA service

Number of Pages Required

3 page

Font styles to use
Sans Serif

Colors

Designer to choose colors to be used in the design.

Requirements
Must have
• The website should have several sections to introduce the services, blog, team introduction, downloads

```html
<!DOCTYPE html>
<html lang="en">
<head>
<meta charset="utf-8">
<title>Kestrova – Remote DBA</title>
<link href="https://fonts.googleapis.com/css2?family=Raleway:wght@400;600;700;800&family=Mulish:wght@400;600;700&display=swap" rel="stylesheet">
<style>
:root{
  --orange:#f7821b;
  --ink:#111318;
  --body:#555a63;
  --light:#f6f6f7;
  --footer:#1f1e2f;
  --footer-text:#a7a6b5;
  --white:#fff;
}
*{box-sizing:border-box;margin:0;padding:0}
html,body{width:1200px;height:3593px;overflow:hidden}
body{font-family:"Mulish",sans-serif;color:var(--body);background:var(--white)}
section,header,footer{position:relative;width:1200px;overflow:hidden}
.abs{position:absolute}
h1,h2,h3,.logo,.btn,.nav{font-family:"Raleway",sans-serif}
.btn{position:absolute;display:flex;align-items:center;justify-content:center;font-weight:700;font-size:19px;text-transform:uppercase;border-radius:4px;letter-spacing:.3px}
.btn-fill{background:var(--orange);color:var(--white)}
.section-title{position:absolute;left:0;width:1200px;text-align:center;font-size:40px;font-weight:700;color:var(--ink);text-transform:uppercase}
.section-lead{position:absolute;left:300px;width:600px;text-align:center;font-size:14px;line-height:27px;color:#444}

/* hero */
.hero{height:678px;background:linear-gradient(110deg,#1d2430 0%,#3a4250 35%,#2a313c 60%,#11151c 100%)}
.hero-photo{inset:0}
.logo{font-weight:800;font-size:42px;color:var(--orange);letter-spacing:.5px}
.hero .logo{left:77px;top:22px}
.nav{position:absolute;top:38px;right:79px;display:flex;gap:32px;font-size:16px;color:var(--white);text-transform:uppercase}
.nav .active{color:var(--orange)}
.hero h1{position:absolute;top:255px;left:0;width:1200px;text-align:center;color:var(--white);font-size:41px;font-weight:700}
.hero .tagline{position:absolute;top:312px;left:0;width:1200px;text-align:center;color:var(--orange);font-family:"Raleway",sans-serif;font-size:28px;text-transform:uppercase}
.hero .intro{position:absolute;top:364px;left:256px;width:688px;text-align:center;color:#e6e8ec;font-size:14px;line-height:29px}
.btn-ghost{background:var(--white);color:var(--orange);border:2px solid var(--orange)}

/* welcome */
.welcome{height:481px;background:var(--white)}
.welcome h2{position:absolute;left:79px;top:736px;top:58px;font-size:40px;font-weight:700;color:var(--ink)}
.welcome .copy{position:absolute;left:79px;top:126px;width:605px;font-size:14px;line-height:28px}
.welcome .copy p{margin-bottom:15px}
.welcome-art{left:718px;top:64px;width:384px;height:372px;border-radius:6px;background:linear-gradient(160deg,#dfe5ee,#9aa6b8 60%,#f1f3f6)}

/* services */
.services{height:585px;background:linear-gradient(180deg,#e9ebee,#f6f7f8 40%,#e2e5e9)}
.services .section-title{top:58px}
.services .section-lead{top:112px}
.service{position:absolute;top:190px;width:340px;text-align:center}
.service .icon{width:124px;height:124px;border-radius:50%;background:var(--white);margin:0 auto;display:flex;align-items:center;justify-content:center;box-shadow:0 2px 8px rgba(0,0,0,.08)}
.service h3{margin-top:38px;font-size:17px;font-weight:700;color:var(--ink);text-transform:uppercase}
.service p{margin-top:8px;font-size:14px;line-height:28px;color:#444;padding:0 14px}
.service .btn{position:relative;margin:22px auto 0;width:168px;height:51px;font-size:18px}

/* blog */
.blog{height:627px;background:var(--white)}
.blog .section-title{top:64px}
.blog .section-lead{top:120px}
.blog-tile{top:198px;width:348px;height:364px}
.tile-1{left:79px;background:linear-gradient(180deg,#b9cde0,#6d8fae 70%,#d8e2ec)}
.tile-2{left:427px;background:linear-gradient(160deg,#c9762f,#e3802a 60%,#b56620)}
.tile-3{left:775px;background:linear-gradient(140deg,#e7ecf1,#9fb1c4 60%,#dfe6ee)}
.tile-2 .overlay{position:absolute;inset:0;background:rgba(247,130,27,.78);text-align:center}
.date-chip{position:absolute;left:84px;top:108px;width:180px;height:50px;background:var(--white);color:var(--orange);border-radius:3px;font-family:"Raleway",sans-serif;font-weight:700;font-size:21px;display:flex;align-items:center;justify-content:center;gap:10px}
.tile-2 h3{position:absolute;top:176px;left:40px;width:268px;color:var(--white);font-size:21px;line-height:30px;font-weight:700}

/* team */
.team{height:546px;background:var(--light)}
.team .section-title{top:60px}
.member{position:absolute;top:136px;width:312px;height:343px;background:var(--white);box-shadow:0 2px 10px rgba(0,0,0,.07);text-align:center}
.member .photo{height:240px;background:linear-gradient(180deg,#c8ccd2,#8e959f)}
.member-2 .photo{background:linear-gradient(180deg,#a5523d,#6d3b33 60%,#38425a)}
.member .socials{position:absolute;top:218px;left:0;width:100%;display:flex;justify-content:center;gap:14px}
.member .socials span{width:44px;height:44px;border-radius:50%;background:var(--white);border:3px solid var(--white);box-shadow:0 1px 5px rgba(0,0,0,.15);position:relative}
.member .socials span::after{content:"";position:absolute;inset:6px;border-radius:50%;background:var(--orange)}
.member h3{margin-top:44px;font-size:19px;font-weight:700;color:var(--ink);text-transform:uppercase}
.member p{font-size:15px;color:#777}

/* download */
.download{height:335px;background:var(--orange)}
.download h2{position:absolute;top:62px;left:0;width:1200px;text-align:center;color:var(--white);font-size:40px;font-weight:600;text-transform:uppercase}
.download .lead{position:absolute;top:118px;left:250px;width:700px;text-align:center;color:#fff2e6;font-size:14px;line-height:28px}
.doc-mark{left:455px;top:196px;width:78px;height:84px;background:#d9501f;border-radius:6px}
.btn-outline{left:544px;top:211px;width:206px;height:52px;border:2px solid var(--white);color:var(--white);font-size:18px}

/* footer */
.site-footer{height:341px;background:var(--footer);color:var(--footer-text)}
.site-footer .logo{left:79px;top:60px}
.about{left:79px;top:118px;width:400px;font-size:14px;line-height:28px}
.foot-social{left:79px;top:195px;display:flex;gap:10px}
.foot-social span{width:38px;height:38px;border-radius:50%;background:var(--orange)}
.site-footer h4{font-family:"Raleway",sans-serif;font-size:18px;font-weight:700;color:var(--orange);text-transform:uppercase}
.sitemap{left:575px;top:56px}
.sitemap ul{list-style:none;margin-top:20px}
.sitemap li{font-size:14px;line-height:29px;padding-left:18px;position:relative}
.sitemap li::before{content:"";position:absolute;left:0;top:12px;width:6px;height:6px;background:var(--orange)}
.contact{left:790px;top:56px}
.contact .row{display:flex;gap:18px;margin-top:20px;font-size:14px;line-height:22px}
.contact .row svg{flex:none;margin-top:2px}
.contact strong{color:var(--orange);display:block;font-weight:700}
.bottom-bar{left:0;top:281px;width:1200px;border-top:1px solid #33324a;padding:18px 79px 0;display:flex;justify-content:space-between;font-size:14px}
.bottom-bar b{color:var(--orange)}
</style>
</head>
<body>

<header class="hero">
  <div class="abs hero-photo" role="img" aria-label="Engineer working in a server room aisle"></div>
  <div class="abs logo">KESTROVA</div>
  <nav class="nav"><span class="active">Home</span><span>About</span><span>Services</span><span>Blog</span><span>Contact</span></nav>
  <h1>THE DATA-DRIVEN PROBLEM SOLVER</h1>
  <div class="tagline">Nearly every business needs</div>
  <p class="intro">Lorem Ipsum is simply dummy text of the printing and typesetting industry. Lorem Ipsum has been the industry's standard dummy text ever since the when an unknown.</p>
  <div class="btn btn-fill" style="left:419px;top:440px;width:187px;height:56px">Learn more</div>
  <div class="btn btn-ghost" style="left:615px;top:440px;width:187px;height:56px">Learn more</div>
</header>

<section class="welcome">
  <h2>WELCOME TO KESTROVA</h2>
  <div class="copy">
    <p>Lorem Ipsum is simply dummy text of the printing and typesetting industry. Lorem Ipsum has been the industry's standard dummy text ever since.</p>
    <p>Lorem Ipsum is simply dummy text of the printing and typesetting industry. Lorem Ipsum has been the industry's standard dummy text ever since the 1500s, when an unknown printer took a galley of type and scrambled it to make a type specimen book.</p>
    <p>Lorem Ipsum is simply dummy text of the printing and typesetting industry. Lorem Ipsum has been the industry's standard dummy text ever since.</p>
  </div>
  <div class="btn btn-fill" style="left:79px;top:359px;width:175px;height:55px">Learn more</div>
  <div class="abs welcome-art" role="img" aria-label="Laptop with document binders rising from the screen"></div>
</section>

<section class="services" role="region" aria-label="Our services">
  <h2 class="section-title">Our Services</h2>
  <p class="section-lead">Lorem Ipsum is simply dummy text of the printing and typesetting industry. Lorem Ipsum has been the industry's standard dummy text ever since.</p>

  <div class="service" style="left:79px">
    <div class="icon"><svg width="60" height="60" viewBox="0 0 60 60"><path d="M8 12h16l4 5h24v26H8z" fill="#1b1d24"/><rect x="17" y="24" width="26" height="4" fill="#fff"/><rect x="17" y="31" width="26" height="4" fill="#fff"/><path d="M30 43v8M14 51h32" stroke="#1b1d24" stroke-width="3"/></svg></div>
    <h3>Remote Database</h3>
    <p>Lorem Ipsum is simply dummy text of the printing and typesetting industry. Lorem Ipsum has been the industry's standard</p>
    <div class="btn btn-fill">Learn more</div>
  </div>
  <div class="service" style="left:430px">
    <div class="icon"><svg width="64" height="64" viewBox="0 0 64 64"><rect x="6" y="26" width="22" height="8" fill="#1b1d24"/><rect x="6" y="37" width="22" height="8" fill="#1b1d24"/><rect x="6" y="48" width="22" height="8" fill="#1b1d24"/><path d="M34 8h10l3 4h11v14H34z" fill="#1b1d24"/><path d="M28 30h16V26M28 52h16v-8" stroke="#1b1d24" stroke-width="2.5" fill="none"/><circle cx="48" cy="42" r="6" fill="#1b1d24"/></svg></div>
    <h3>Data Platform Administration</h3>
    <p>Lorem Ipsum is simply dummy text of the printing and typesetting industry. Lorem Ipsum has been the industry's standard</p>
    <div class="btn btn-fill">Learn more</div>
  </div>
  <div class="service" style="left:782px">
    <div class="icon"><svg width="62" height="62" viewBox="0 0 62 62"><rect x="6" y="10" width="50" height="34" rx="3" fill="#1b1d24"/><rect x="11" y="15" width="40" height="24" fill="#fff"/><path d="M24 22l-6 5 6 5M38 22l6 5-6 5" stroke="#1b1d24" stroke-width="2.5" fill="none"/><circle cx="28" cy="27" r="1.6" fill="#1b1d24"/><circle cx="34" cy="27" r="1.6" fill="#1b1d24"/><path d="M31 44v8M20 52h22" stroke="#1b1d24" stroke-width="3"/></svg></div>
    <h3>Development</h3>
    <p>Lorem Ipsum is simply dummy text of the printing and typesetting industry. Lorem Ipsum has been the industry's standard</p>
    <div class="btn btn-fill">Learn more</div>
  </div>
</section>

<section class="blog">
  <h2 class="section-title">Our Blog Post</h2>
  <p class="section-lead">Lorem Ipsum is simply dummy text of the printing and typesetting industry. Lorem Ipsum has been the industry's standard dummy text ever since.</p>
  <div class="abs blog-tile tile-1" role="img" aria-label="Person with umbrella facing a digital key in blue data rain"></div>
  <div class="abs blog-tile tile-2" role="img" aria-label="Engineer working on a laptop, orange overlay">
    <div class="overlay">
      <div class="date-chip"><svg width="18" height="18" viewBox="0 0 18 18"><rect x="1.5" y="3" width="15" height="13.5" fill="none" stroke="#f7821b" stroke-width="2"/><path d="M1.5 7h15M5 1v4M13 1v4" stroke="#f7821b" stroke-width="2"/></svg>04 Sep 2018</div>
      <h3>Lorem Ipsum is simple text of print and type industry</h3>
      <svg class="abs" style="left:155px;top:262px" width="36" height="18" viewBox="0 0 36 18"><path d="M2 9h28M22 2l8 7-8 7" stroke="#fff" stroke-width="3" fill="none"/></svg>
    </div>
  </div>
  <div class="abs blog-tile tile-3" role="img" aria-label="Hand touching a data network button connected to user icons"></div>
</section>

<section class="team">
  <h2 class="section-title">Our Team</h2>
  <div class="member" style="left:280px">
    <div class="photo" role="img" aria-label="Portrait of a team member in a suit"></div>
    <div class="socials"><span></span><span></span><span></span></div>
    <h3>Client Name</h3><p>kestrova.cz</p>
  </div>
  <div class="member member-2" style="left:611px">
    <div class="photo" role="img" aria-label="Portrait of a team member in front of a brick wall"></div>
    <div class="socials"><span></span><span></span><span></span></div>
    <h3>Client Name</h3><p>kestrova.cz</p>
  </div>
</section>

<section class="download">
  <h2>Download</h2>
  <p class="lead">Lorem Ipsum is simply dummy text of the printing and typesetting industry. Lorem Ipsum has been the industry's standard dummy text ever since the when an unknown printer.</p>
  <div class="abs doc-mark" role="img" aria-label="Presentation document"></div>
  <div class="btn btn-outline">Download now</div>
</section>

<footer class="site-footer">
  <div class="abs logo">KESTROVA</div>
  <p class="abs about">Lorem Ipsum is simply dummy text of the printing and typesetting industry. Lorem Ipsum has been the industry's standard dummy text ever since.</p>
  <div class="abs foot-social"><span></span><span></span><span></span></div>
  <div class="abs sitemap">
    <h4>Sitemap</h4>
    <ul><li>Home</li><li>About</li><li>Services</li><li>Blog</li><li>Contact</li></ul>
  </div>
  <div class="abs contact">
    <h4>Contact Us</h4>
    <div class="row"><svg width="16" height="22" viewBox="0 0 16 22"><path d="M8 0a8 8 0 0 0-8 8c0 6 8 14 8 14s8-8 8-14a8 8 0 0 0-8-8z" fill="#f7821b"/><circle cx="8" cy="8" r="3" fill="#1f1e2f"/></svg><div><strong>KESTROVA</strong>101 - Lorem ipsum is simple dummy<br>text of print type industry.</div></div>
    <div class="row"><svg width="18" height="18" viewBox="0 0 18 18"><path d="M4 1l3 4-2 2c1 2 3 4 5 5l2-2 4 3-2 3C8 16 2 10 1 4z" fill="#f7821b"/></svg><div>+420 555 010 200</div></div>
    <div class="row"><svg width="18" height="14" viewBox="0 0 18 14"><rect width="18" height="14" rx="1" fill="#f7821b"/><path d="M1 1l8 7 8-7" stroke="#1f1e2f" stroke-width="1.6" fill="none"/></svg><div>info@kestrova.cz</div></div>
  </div>
  <div class="abs bottom-bar"><span>©<b>KESTROVA</b> - 2018 All Rights Reserved</span><span>Terms and conditions &nbsp;|&nbsp; Privacy Policy</span></div>
</footer>

</body>
</html>
```